Business Card

Just need business logo with phone number on it. 0487 312 654
And the following on the bottom of the card.

"Your local plumbing experts".
and emblems for zelpa card, cheque and cash

```html
<!DOCTYPE html>
<html lang="en">
<head>
<meta charset="utf-8">
<title>Harbour Bend Plumbing &amp; Drainage – Business Card</title>
<link rel="stylesheet" href="https://fonts.googleapis.com/css2?family=Exo+2:wght@400;600;800&display=swap">
<style>
  :root {
    --brand-red: #ec1f2b;
    --brand-blue: #1a8fce;
    --card-white: #ffffff;
    --stage: #ecebe8;
    --ink: #111111;
    --shadow: rgba(0, 0, 0, 0.18);
  }
  * { box-sizing: border-box; margin: 0; padding: 0; }
  html, body {
    width: 1200px;
    height: 900px;
    overflow: hidden;
    background: var(--stage);
    font-family: "Exo 2", "Helvetica Neue", Arial, sans-serif;
  }
  .stage { position: relative; width: 1200px; height: 900px; }

  .card {
    position: absolute;
    overflow: hidden;
    box-shadow: 0 6px 18px var(--shadow);
  }

  /* Front */
  .card-front {
    left: 178px; top: 74px;
    width: 588px; height: 364px;
    background: var(--brand-red);
    color: var(--card-white);
  }
  .front-split { position: absolute; inset: 0; }
  .front-wordmark {
    position: absolute;
    right: 36px; top: 54px;
    font-weight: 800;
    font-size: 62px;
    letter-spacing: 2px;
    line-height: 1;
    color: var(--card-white);
  }
  .front-phone {
    position: absolute;
    right: 36px; top: 162px;
    display: flex; align-items: center; gap: 10px;
    font-size: 23px; font-weight: 400; letter-spacing: 0.5px;
  }
  .front-phone svg { width: 32px; height: 32px; }
  .front-tagline {
    position: absolute;
    right: 36px; top: 226px;
    text-align: right;
    font-size: 22px; line-height: 28px;
  }
  .payment-list {
    position: absolute;
    right: 36px; top: 294px;
    display: flex; gap: 12px;
    list-style: none;
  }
  .payment-item {
    width: 64px; height: 38px;
    background: var(--card-white);
    display: flex; align-items: center; justify-content: center;
  }
  .payment-item svg { display: block; }
  .payment-card-name {
    font-weight: 800; font-size: 15px; color: var(--brand-blue);
    letter-spacing: 0.5px;
  }
  .payment-item.cheque { background: transparent; }

  /* Back */
  .card-back {
    left: 388px; top: 506px;
    width: 567px; height: 351px;
    background: var(--card-white);
  }
  .back-band-top {
    position: absolute; left: 0; right: 0; top: 0; height: 16px;
    background: var(--brand-blue);
  }
  .back-band-bottom {
    position: absolute; left: 0; right: 0; bottom: 0; height: 16px;
    background: var(--brand-red);
  }
  .back-logo {
    position: absolute;
    left: 0; right: 0; top: 132px;
    text-align: center;
    color: var(--brand-red);
    font-weight: 800;
  }
  .back-logo-initials { font-size: 44px; line-height: 1; letter-spacing: 2px; }
  .back-logo-name {
    margin-top: 6px;
    font-size: 20px; line-height: 22px; letter-spacing: 1px;
    text-transform: uppercase;
  }
</style>
</head>
<body>
<main class="stage">

  <section class="card card-front" aria-label="Business card front">
    <svg class="front-split" viewBox="0 0 588 364" aria-hidden="true">
      <path d="M0 0 H180 C150 60 95 120 80 190 C62 270 110 340 180 364 H0 Z" fill="var(--brand-blue)"/>
    </svg>

    <div class="front-wordmark">HBPD</div>

    <div class="front-phone">
      <span>0487 312 654</span>
      <svg viewBox="0 0 32 32" aria-hidden="true">
        <circle cx="16" cy="16" r="14" fill="none" stroke="currentColor" stroke-width="2"/>
        <path d="M9 13c0-2 3-3 7-3s7 1 7 3v1.5h-3.2v-1.5h-7.6v1.5H9z" fill="currentColor"/>
        <path d="M11 15h10l1.5 7h-13z" fill="currentColor"/>
        <circle cx="16" cy="18.5" r="1.8" fill="var(--brand-red)"/>
      </svg>
    </div>

    <p class="front-tagline">Your local<br>plumbing experts</p>

    <ul class="payment-list" aria-label="Payment methods accepted">
      <li class="payment-item card-pay"><span class="payment-card-name">ZELPA</span></li>
      <li class="payment-item cash">
        <svg width="26" height="26" viewBox="0 0 26 26" aria-label="Cash">
          <circle cx="13" cy="13" r="11" fill="var(--ink)"/>
          <text x="13" y="18" text-anchor="middle" font-size="14" font-weight="800" fill="#fff" font-family="Exo 2, sans-serif">$</text>
        </svg>
      </li>
      <li class="payment-item cheque">
        <svg width="64" height="38" viewBox="0 0 64 38" aria-label="Cheque">
          <rect x="4" y="6" width="56" height="26" fill="none" stroke="#fff" stroke-width="1.5"/>
          <rect x="1" y="3" width="56" height="26" fill="var(--brand-red)" stroke="#fff" stroke-width="1.5"/>
          <line x1="6" y1="10" x2="52" y2="10" stroke="#fff" stroke-width="1.2"/>
          <rect x="34" y="14" width="18" height="5" fill="none" stroke="#fff" stroke-width="1.2"/>
          <line x1="6" y1="23" x2="24" y2="23" stroke="#fff" stroke-width="1.2"/>
          <line x1="34" y1="23" x2="52" y2="23" stroke="#fff" stroke-width="1.2"/>
        </svg>
      </li>
    </ul>
  </section>

  <section class="card card-back" aria-label="Business card back">
    <div class="back-band-top"></div>
    <div class="back-logo">
      <div class="back-logo-initials">HBPD</div>
      <div class="back-logo-name">Harbour Bend<br>Plumbing &amp; Drainage</div>
    </div>
    <div class="back-band-bottom"></div>
  </section>

</main>
</body>
</html>
```